Business card design and logo needed - Photographer

I take photos of weddings, rodeos, snowmobiling.
Need a card to hand out to prospective clients.
Industry/Entity Type
Business
Contact Information for Business Card
Marcus Tollen Photography
Requirements
Must have
- Bold
Black or white base.
My website. www.MarcusTollen-example.com
Should not have
- camera/ lens/ aperture blades

```html
<!DOCTYPE html>
<html lang="en">
<head>
<meta charset="utf-8">
<title>Marcus Tollen Photography – Business Card</title>
<link href="https://fonts.googleapis.com/css2?family=Inter:wght@800&family=Cormorant+SC:wght@600&display=swap" rel="stylesheet">
<style>
  :root {
    --backdrop: #eceff0;
    --card-white: #ffffff;
    --card-black: #0a0b0b;
    --watermark-grey: #e6e9ea;
    --ink-light: #f4f4f4;
    --ink-muted: #d2d4d5;
  }
  html, body {
    margin: 0;
    padding: 0;
    width: 1200px;
    height: 900px;
    overflow: hidden;
    background: var(--backdrop);
  }
  .canvas {
    position: relative;
    width: 1200px;
    height: 900px;
  }
  .business-card {
    position: absolute;
    left: 132px;
    top: 192px;
    width: 936px;
    height: 516px;
    background: var(--card-white);
    overflow: hidden;
  }
  .name-band {
    position: absolute;
    left: 0;
    top: 0;
    width: 100%;
    height: 232px;
    overflow: hidden;
  }
  .name-wordmark {
    position: absolute;
    left: -4px;
    bottom: -30px;
    margin: 0;
    font-family: "Inter", "Helvetica Neue", Arial, sans-serif;
    font-weight: 800;
    font-size: 150px;
    line-height: 1;
    letter-spacing: -0.05em;
    color: var(--watermark-grey);
    white-space: nowrap;
  }
  .contact-band {
    position: absolute;
    left: 0;
    top: 232px;
    width: 100%;
    height: 284px;
    background: var(--card-black);
    text-align: center;
    font-family: "Cormorant SC", "Times New Roman", serif;
    font-weight: 600;
  }
  .studio-name {
    margin: 0;
    position: absolute;
    left: 0;
    right: 0;
    top: 86px;
    font-size: 23px;
    letter-spacing: 0.04em;
    color: var(--ink-light);
    text-transform: uppercase;
  }
  .contact-list {
    list-style: none;
    margin: 0;
    padding: 0;
    position: absolute;
    left: 0;
    right: 0;
    top: 142px;
    font-size: 18px;
    line-height: 31px;
    letter-spacing: 0.03em;
    color: var(--ink-muted);
  }
</style>
</head>
<body>
  <main class="canvas">
    <article class="business-card">
      <div class="name-band" aria-hidden="true">
        <p class="name-wordmark">MarcusTollen</p>
      </div>
      <section class="contact-band">
        <h1 class="studio-name">Marcus Tollen Photography</h1>
        <ul class="contact-list">
          <li class="contact-phone">555.014.2290</li>
          <li class="contact-web">www.MarcusTollen-example.com</li>
          <li class="contact-social">www.social-example.com/marcus.tollen</li>
        </ul>
      </section>
    </article>
  </main>
</body>
</html>
```